Business Cards for a law firm

Business cards for our law firm. Use our silhoette logo and OAK PARTNERS - check our website (www.oakpartners.example)

Contact Information for Business Card

our silhouette logo, OAK PARTNERS, 800-555-0147, Dorian Pemberton, dorian@oakpartners.example

Requirements
Must have
• our silhouette logo, OAK PARTNERS, 800-555-0147, Dorian Pemberton, dorian@oakpartners.example

```html
<!DOCTYPE html>
<html lang="en">
<head>
<meta charset="utf-8">
<title>Oak Partners – Business Cards</title>
<link rel="stylesheet" href="https://fonts.googleapis.com/css2?family=Montserrat:wght@700&family=Open+Sans:wght@400;600;700&display=swap">
<style>
  :root {
    --navy: #1f2f63;
    --paper: #f2f2f2;
    --backdrop: #cfcfcf;
    --accent: #f0a019;
    --ink-grey: #6b6b6b;
    --white: #ffffff;
  }
  * { margin: 0; padding: 0; box-sizing: border-box; }
  html, body { width: 1200px; height: 853px; overflow: hidden; }
  body {
    background: var(--backdrop);
    font-family: "Open Sans", sans-serif;
    position: relative;
  }
  .card {
    position: absolute;
    top: 278px;
    width: 520px;
    height: 297px;
    border-radius: 22px;
    overflow: hidden;
  }
  .card-front { left: 60px; background: var(--paper); }
  .card-back {
    left: 620px;
    background: var(--navy);
    display: flex;
    align-items: center;
    justify-content: center;
  }

  .brand { display: flex; align-items: center; gap: 12px; }
  .brand-mark { width: 26px; height: 26px; flex: none; }
  .wordmark {
    font-family: "Montserrat", sans-serif;
    font-weight: 700;
    letter-spacing: 0.04em;
    white-space: nowrap;
    line-height: 1;
  }
  .card-front .brand { position: absolute; left: 36px; top: 30px; }
  .card-front .brand-mark { background: var(--navy); }
  .card-front .wordmark { font-size: 24px; color: var(--navy); }
  .card-back .brand-mark { background: var(--white); width: 32px; height: 32px; }
  .card-back .wordmark { font-size: 30px; color: var(--white); }

  .figure-panel { position: absolute; right: 0; bottom: 0; width: 260px; height: 297px; }

  .details { position: absolute; left: 36px; top: 104px; }
  .firm-name {
    font-family: "Montserrat", sans-serif;
    font-weight: 700;
    font-size: 15px;
    color: var(--navy);
    letter-spacing: 0.02em;
  }
  .firm-tagline { font-size: 8px; letter-spacing: 0.32em; color: var(--navy); margin-top: 1px; }
  .rule { width: 20px; height: 2px; background: var(--accent); margin: 9px 0 8px; }
  .person-name {
    font-weight: 700;
    font-size: 12px;
    color: var(--navy);
    letter-spacing: 0.03em;
    text-transform: uppercase;
  }
  .person-title { font-size: 10px; color: var(--ink-grey); letter-spacing: 0.08em; }
  .contact { margin-top: 10px; list-style: none; }
  .contact li {
    display: flex;
    align-items: center;
    gap: 7px;
    font-size: 10px;
    color: var(--ink-grey);
    margin-bottom: 5px;
    white-space: nowrap;
  }
  .contact svg { width: 11px; height: 11px; flex: none; }
</style>
</head>
<body>
  <section class="card card-front">
    <div class="brand">
      <span class="brand-mark" aria-hidden="true"></span>
      <span class="wordmark">OAK PARTNERS</span>
    </div>

    <div class="details">
      <div class="firm-name">OAK PARTNERS</div>
      <div class="firm-tagline">INJURY ATTORNEYS</div>
      <div class="rule"></div>
      <div class="person-name">Dorian Pemberton</div>
      <div class="person-title">ATTORNEY</div>
      <ul class="contact">
        <li>
          <svg viewBox="0 0 12 12" aria-hidden="true"><path d="M3 1 L5 3.5 L4 5 Q5 7 7 8 L8.5 7 L11 9 L9.5 11 Q4 10.5 1 3 Z" fill="var(--accent)"/></svg>
          800-555-0147
        </li>
        <li>
          <svg viewBox="0 0 12 12" aria-hidden="true"><rect x="1" y="2.5" width="10" height="7" fill="var(--accent)"/><path d="M1 2.5 L6 6.5 L11 2.5" fill="none" stroke="#fff" stroke-width="1"/></svg>
          dorian@oakpartners.example
        </li>
        <li>
          <svg viewBox="0 0 12 12" aria-hidden="true"><circle cx="6" cy="6" r="4.6" fill="none" stroke="var(--accent)" stroke-width="1.2"/><ellipse cx="6" cy="6" rx="2" ry="4.6" fill="none" stroke="var(--accent)" stroke-width="1"/><path d="M1.4 6 H10.6" stroke="var(--accent)" stroke-width="1"/></svg>
          www.oakpartners.example
        </li>
      </ul>
    </div>

    <svg class="figure-panel" viewBox="0 0 260 297" role="img" aria-label="Two standing figures shown as white silhouettes on a navy field">
      <path d="M20 297 L40 230 Q60 150 95 105 Q120 60 160 40 L260 40 L260 297 Z" fill="var(--navy)"/>
    </svg>
  </section>

  <section class="card card-back">
    <div class="brand">
      <span class="brand-mark" aria-hidden="true"></span>
      <span class="wordmark">OAK PARTNERS</span>
    </div>
  </section>
</body>
</html>
```